KOVA! Card

The single side "business card" will be utilized to write down product information for our customers. The card needs to include our logo in josefin font and read KOVA! on the front. Our brand colors are espresso brown and copper. The back needs to be white (blank) to allow us to write information down. We want modern, bold, clean and fun.
I have attached a copy of our logo but you do not have to utilize exactly as shown.

```html
<!DOCTYPE html>
<html lang="en">
<head>
<meta charset="utf-8">
<title>KOVA! Card – Front and Back</title>
<link href="https://fonts.googleapis.com/css2?family=Josefin+Sans:wght@400&display=swap" rel="stylesheet">
<style>
  :root {
    --copper: #c4651f;
    --espresso: #2a1610;
    --paper: #ffffff;
    --backdrop: #e8e6e9;
    --rule: #d99a6c;
  }
  * { box-sizing: border-box; margin: 0; padding: 0; }
  html, body {
    width: 1200px;
    height: 900px;
    overflow: hidden;
    background: var(--backdrop);
    font-family: "Josefin Sans", sans-serif;
    font-weight: 400;
  }
  .sheet {
    position: relative;
    width: 1200px;
    height: 900px;
  }
  .card {
    position: absolute;
    top: 313px;
    width: 480px;
    height: 274px;
    overflow: hidden;
    box-shadow: 0 6px 16px rgba(40, 30, 40, 0.25);
  }
  .card--front { left: 90px; background: var(--copper); }
  .card--back  { left: 630px; background: var(--paper); }

  .brand { position: absolute; white-space: nowrap; }
  .brand__name {
    display: block;
    line-height: 1;
  }
  .brand__tagline {
    display: block;
    line-height: 1;
  }

  .card--front .brand { left: 132px; top: 82px; color: var(--espresso); }
  .card--front .brand__name { font-size: 44px; }
  .card--front .brand__tagline { font-size: 16px; margin-top: 12px; }

  .headline {
    position: absolute;
    right: 26px;
    bottom: 26px;
    color: var(--espresso);
    font-size: 40px;
    line-height: 1;
    letter-spacing: 0.03em;
    white-space: nowrap;
  }

  .card--back .brand { left: 362px; top: 28px; color: var(--copper); }
  .card--back .brand__name { font-size: 18px; }
  .card--back .brand__tagline { font-size: 7.5px; margin-top: 4px; }

  .note-lines {
    position: absolute;
    left: 30px;
    top: 0;
    width: 418px;
    height: 274px;
  }
</style>
</head>
<body>
  <main class="sheet">
    <section class="card card--front" aria-label="Card front">
      <div class="brand">
        <span class="brand__name">Ambrels</span>
        <span class="brand__tagline">Jewelry &amp; Design Studio</span>
      </div>
      <p class="headline">KOVA!</p>
    </section>

    <section class="card card--back" aria-label="Card back for handwritten notes">
      <div class="brand">
        <span class="brand__name">Ambrels</span>
        <span class="brand__tagline">Jewelry &amp; Design Studio</span>
      </div>
      <svg class="note-lines" viewBox="0 0 418 274" aria-hidden="true">
        <g stroke="var(--rule)" stroke-width="1">
          <line x1="0" y1="90.5"  x2="418" y2="90.5"/>
          <line x1="0" y1="121.5" x2="418" y2="121.5"/>
          <line x1="0" y1="152.5" x2="418" y2="152.5"/>
          <line x1="0" y1="183.5" x2="418" y2="183.5"/>
          <line x1="0" y1="214.5" x2="418" y2="214.5"/>
          <line x1="0" y1="246.5" x2="418" y2="246.5"/>
        </g>
      </svg>
    </section>
  </main>
</body>
</html>
```